Brisbane IT support business needs our first website

Hi All,

We are after a new website design for our IT solutions and support business.The business name is Harbourline Computing Services Group, or HCSG for short. We provide a range of solutions and services within the IT space.

I would like to utilize the two colours in our business logo I have uploaded.

I understand this is initially for the design only aspect of the site, but I would like to engage the winner to finish coding the website and finalize after also.

Target Market(s)

Other businesses owners and home users.

Industry/Entity Type

Business

Requirements
Must have
• Nice clean and functional design utilizing our business colours from the logo.

```html
<!DOCTYPE html>
<html lang="en">
<head>
<meta charset="utf-8">
<title>HCSG – IT Solutions &amp; Support</title>
<link href="https://fonts.googleapis.com/css2?family=Open+Sans:wght@400;600;700&display=swap" rel="stylesheet">
<style>
:root{
  --teal:#1d5b76;
  --teal-dark:#174a60;
  --orange:#f08a24;
  --orange-dark:#d9731a;
  --ink:#333;
  --muted:#777;
  --dark:#1b1b1b;
  --panel:#2a2a2a;
  --light:#f2f2f2;
  --white:#fff;
}
*{box-sizing:border-box;margin:0;padding:0}
html,body{width:1200px;height:2748px;overflow:hidden}
body{font-family:"Open Sans",Arial,sans-serif;color:var(--ink);background:var(--white);font-size:15px}
section,header{position:relative;width:1200px}
.row{display:flex;align-items:center}

/* header */
.site-header{height:112px;background:var(--white);border-bottom:1px solid #e5e5e5}
.brand{position:absolute;left:40px;top:16px;display:flex;align-items:center;gap:14px}
.brand-mark{width:78px;height:78px;border-radius:50%;background:var(--teal)}
.brand-name{font-size:44px;font-weight:700;color:var(--orange);line-height:1}
.brand-tag{font-size:11px;font-weight:600;color:var(--teal);letter-spacing:1px;margin-top:4px}
.top-contact{position:absolute;right:40px;top:12px;gap:28px;font-size:15px;color:var(--teal)}
.top-contact .item{display:flex;align-items:center;gap:8px}
.top-contact .ico{width:26px;height:26px;border-radius:4px;background:var(--orange);display:flex;align-items:center;justify-content:center}
.top-contact .phone{font-size:24px;font-weight:600}
.main-nav{position:absolute;right:40px;top:66px;gap:6px}
.main-nav a{font-size:14px;font-weight:600;color:var(--teal);text-decoration:none;padding:6px 14px}
.main-nav a.active{color:var(--orange);border-bottom:3px solid var(--orange)}

/* hero */
.hero{height:480px;background:radial-gradient(ellipse at 72% 60%,#3d4b55 0%,#161b20 60%,#0c0f12 100%)}
.hero-photo{position:absolute;left:560px;top:0;width:640px;height:480px;background:radial-gradient(ellipse at 55% 55%,rgba(150,180,200,.35),rgba(20,25,30,0) 65%)}
.hero-copy{position:absolute;left:160px;top:120px;width:460px;color:var(--white)}
.hero-copy h1{font-size:52px;font-weight:700;line-height:1.05}
.hero-copy h2{font-size:40px;font-weight:400;color:var(--orange);line-height:1.2;white-space:nowrap}
.hero-copy p{font-size:14px;font-weight:600;line-height:1.5;margin:14px 0 22px;width:380px}
.btn{display:inline-block;background:var(--orange);color:var(--white);font-weight:700;font-size:15px;padding:10px 20px;border-radius:3px}
.slide-arrow{position:absolute;top:218px;width:44px;height:44px;border-radius:50%;background:rgba(255,255,255,.18);display:flex;align-items:center;justify-content:center}
.slide-arrow.prev{left:40px}.slide-arrow.next{right:40px}

/* intro */
.intro{height:188px;padding:28px 150px;text-align:center;font-size:15px;line-height:1.7;color:var(--muted)}

/* services */
.services{height:252px;background:var(--teal);color:var(--white);text-align:center;padding-top:34px}
.section-title{font-size:34px;font-weight:400;letter-spacing:1px}
.section-sub{font-size:17px;margin-top:2px}
.service-list{justify-content:center;gap:26px;margin-top:30px}
.service-card{width:208px;height:84px;background:var(--white);border-radius:4px;color:var(--ink);display:flex;align-items:center;gap:14px;padding:0 16px;text-align:left;font-size:15px;font-weight:600;line-height:1.25}
.service-card .ico{width:48px;height:48px;border-radius:50%;border:3px solid var(--teal);flex:none;display:flex;align-items:center;justify-content:center}

/* news */
.news{height:268px;background:var(--teal-dark);padding:40px 156px;display:flex;gap:64px}
.news-card{width:412px;color:#d8e4ea}
.news-date{background:var(--panel);color:var(--white);font-size:13px;font-weight:600;padding:8px 14px;display:flex;gap:8px;align-items:center}
.news-title{background:#6b7f89;color:var(--white);font-size:14px;font-weight:600;padding:8px 14px}
.news-body{font-size:14px;line-height:1.6;padding:12px 14px}

/* solutions */
.solutions{height:280px;background:var(--orange);color:var(--white)}
.solutions-intro{position:absolute;left:156px;top:74px;width:300px}
.solutions-intro h2{font-size:34px;font-weight:400;line-height:1.1}
.solutions-intro h3{font-size:20px;font-weight:400}
.solutions-intro p{font-size:13px;margin-top:10px;line-height:1.5;width:250px}
.dots{display:flex;gap:8px;margin-top:12px}
.dots span{width:12px;height:12px;border-radius:50%;background:rgba(255,255,255,.5)}
.dots span:first-child{background:var(--white)}
.solution-list{position:absolute;left:484px;top:52px;gap:34px}
.solution-card{width:176px;text-align:center;font-size:17px;font-weight:700;line-height:1.25}
.solution-card .tile{width:112px;height:112px;margin:0 auto 14px;border-radius:6px;background:var(--orange-dark);display:flex;align-items:center;justify-content:center;box-shadow:0 2px 0 rgba(0,0,0,.12)}

/* clients */
.clients{height:400px;background:var(--white);text-align:center;padding-top:30px}
.clients .section-title{color:var(--teal)}
.clients-quote{width:940px;margin:20px auto 0;font-size:15px;line-height:1.7;color:var(--muted)}
.client-strip{position:absolute;left:0;top:268px;width:1200px;height:104px;background:var(--light);justify-content:center;gap:40px}
.client-strip .arrow{position:absolute;top:34px;color:#999;font-size:26px}
.client-name{width:190px;height:64px;background:var(--white);display:flex;align-items:center;justify-content:center;font-size:24px;font-weight:700;color:#333}

/* team */
.team{height:260px;display:flex}
.team-intro{width:236px;height:260px;background:var(--dark);color:var(--white);padding:30px 26px}
.team-intro h2{font-size:28px;font-weight:400}
.team-intro p{font-size:13px;line-height:1.55;margin-top:14px}
.team-arrows{display:flex;gap:8px;margin-top:16px}
.team-arrows span{width:32px;height:32px;background:var(--white);display:flex;align-items:center;justify-content:center}
.team-photo{height:260px}

/* contact */
.contact{height:508px;background:var(--dark);color:#ccc}
.contact .section-title{position:absolute;left:0;top:28px;width:1200px;text-align:center;color:var(--white)}
.contact-lead{position:absolute;left:300px;top:88px;width:600px;text-align:center;font-size:15px;line-height:1.6}
.contact-lead a{color:var(--orange);text-decoration:none}
.contact-info{position:absolute;left:120px;top:180px;font-size:13px;line-height:1.6}
.contact-info .line{display:flex;gap:12px;align-items:flex-start;margin-bottom:18px}
.contact-info .phone{font-size:17px;font-weight:700;color:var(--white)}
.social{display:flex;gap:14px;margin-left:40px}
.social span{width:40px;height:40px;border-radius:50%;background:#666}
.contact-form{position:absolute;left:620px;top:182px;width:450px;height:240px}
.field{height:40px;background:var(--panel);border:1px solid #3a3a3a;margin-bottom:12px;font-size:12px;color:#888;padding:11px 12px}
.field.area{height:72px}
.contact-form .btn{position:absolute;right:0;top:190px;padding:10px 22px}
.copyright{position:absolute;left:120px;top:466px;font-size:12px;color:#999}
</style>
</head>
<body>

<header class="site-header">
  <div class="brand">
    <div class="brand-mark"></div>
    <div>
      <div class="brand-name">HCSG</div>
      <div class="brand-tag">TECHNOLOGY SOLUTIONS</div>
    </div>
  </div>
  <div class="top-contact row">
    <div class="item"><span class="ico"><svg width="14" height="10" viewBox="0 0 14 10"><rect x="0.5" y="0.5" width="13" height="9" fill="none" stroke="#fff"/><path d="M1 1l6 5 6-5" fill="none" stroke="#fff"/></svg></span>info@hcsgmail.com</div>
    <div class="item"><span class="ico"><svg width="14" height="14" viewBox="0 0 24 24"><path d="M6 2l4 4-2 3c1 3 4 6 7 7l3-2 4 4-3 4C10 21 3 14 2 5z" fill="#fff"/></svg></span><span class="phone">123-456-7890</span></div>
  </div>
  <nav class="main-nav row">
    <a class="active">HOME</a><a>ABOUT</a><a>SERVICES</a><a>TECHNOLOGY</a><a>SOLUTIONS</a><a>SUPPORT</a><a>CONTACT</a>
  </nav>
</header>

<section class="hero">
  <div class="hero-photo" role="img" aria-label="Photo of an open hand holding glowing technology icons"></div>
  <div class="hero-copy">
    <h1>SUCCESS WITH</h1>
    <h2>Our Creative Solutions</h2>
    <p>Reliable support and smart systems that keep your business running every day.</p>
    <span class="btn">LEARN MORE</span>
  </div>
  <div class="slide-arrow prev"><svg width="14" height="18" viewBox="0 0 14 18"><path d="M11 2L4 9l7 7" fill="none" stroke="#fff" stroke-width="3"/></svg></div>
  <div class="slide-arrow next"><svg width="14" height="18" viewBox="0 0 14 18"><path d="M3 2l7 7-7 7" fill="none" stroke="#fff" stroke-width="3"/></svg></div>
</section>

<section class="intro">
  <p>We help local businesses and home users get more from their technology with friendly advice, fast support and practical solutions. From networks and servers to everyday devices, our team plans, installs and looks after the systems you rely on, so you can focus on the work that matters most to you.</p>
</section>

<section class="services">
  <h2 class="section-title">OUR SERVICES</h2>
  <div class="section-sub">Harbourline IT Solutions</div>
  <div class="service-list row">
    <div class="service-card"><span class="ico"><svg width="22" height="22" viewBox="0 0 22 22"><circle cx="11" cy="9" r="6" fill="none" stroke="#1d5b76" stroke-width="2.5"/><path d="M7 14l-2 7 6-3 6 3-2-7" fill="#1d5b76"/></svg></span>Premium<br>IT Solutions</div>
    <div class="service-card"><span class="ico"><svg width="24" height="20" viewBox="0 0 24 20"><rect x="1" y="1" width="22" height="14" fill="none" stroke="#1d5b76" stroke-width="2.5"/><path d="M8 19h8" stroke="#1d5b76" stroke-width="2.5"/></svg></span>Web<br>Development</div>
    <div class="service-card"><span class="ico"><svg width="20" height="24" viewBox="0 0 20 24"><ellipse cx="10" cy="4" rx="8" ry="3" fill="#1d5b76"/><path d="M2 4v16c0 2 16 2 16 0V4M2 12c0 2 16 2 16 0" fill="none" stroke="#1d5b76" stroke-width="2.5"/></svg></span>Database<br>Management</div>
    <div class="service-card"><span class="ico"><svg width="24" height="22" viewBox="0 0 24 22"><path d="M3 14V11a9 9 0 0118 0v3" fill="none" stroke="#1d5b76" stroke-width="2.5"/><rect x="1" y="12" width="5" height="8" fill="#1d5b76"/><rect x="18" y="12" width="5" height="8" fill="#1d5b76"/></svg></span>Technical<br>Support</div>
  </div>
</section>

<section class="news">
  <article class="news-card">
    <div class="news-date"><svg width="14" height="14" viewBox="0 0 14 14"><rect x="1" y="2" width="12" height="11" fill="none" stroke="#fff" stroke-width="1.5"/><path d="M1 5h12" stroke="#fff" stroke-width="1.5"/></svg>04-March-2014</div>
    <div class="news-title">New cloud backup plans for small offices</div>
    <p class="news-body">Our latest guide covers the steps to keep data safe and systems fast.</p>
  </article>
  <article class="news-card">
    <div class="news-date"><svg width="14" height="14" viewBox="0 0 14 14"><rect x="1" y="2" width="12" height="11" fill="none" stroke="#fff" stroke-width="1.5"/><path d="M1 5h12" stroke="#fff" stroke-width="1.5"/></svg>24-March-2014</div>
    <div class="news-title">Upgrading your home network made simple</div>
    <p class="news-body">We explain how better routers and setup improve speed across every room.</p>
  </article>
</section>

<section class="solutions">
  <div class="solutions-intro">
    <h2>OUR SOLUTIONS</h2>
    <h3>We Take Pride In Our Work</h3>
    <p>Tailored services built around the way your business works.</p>
    <div class="dots"><span></span><span></span></div>
  </div>
  <div class="solution-list row">
    <div class="solution-card"><div class="tile"><svg width="48" height="44" viewBox="0 0 48 44"><path d="M24 2L2 12l22 10 22-10z" fill="#fff"/><path d="M10 17v12c0 6 28 6 28 0V17" fill="none" stroke="#fff" stroke-width="4"/></svg></div>Job<br>Management</div>
    <div class="solution-card"><div class="tile"><svg width="44" height="44" viewBox="0 0 44 44"><circle cx="22" cy="13" r="9" fill="#fff"/><path d="M4 42c2-12 10-16 18-16s16 4 18 16z" fill="#fff"/></svg></div>Business<br>Management</div>
    <div class="solution-card"><div class="tile"><svg width="50" height="44" viewBox="0 0 50 44"><circle cx="16" cy="12" r="7" fill="#fff"/><circle cx="34" cy="12" r="7" fill="#fff"/><path d="M2 40c1-10 7-14 14-14s13 4 14 14zM20 40c1-10 7-14 14-14s13 4 14 14z" fill="#fff"/></svg></div>Customer<br>Relationship</div>
  </div>
</section>

<section class="clients">
  <h2 class="section-title">OUR CLIENTS</h2>
  <p class="clients-quote">Our clients trust us to keep their systems secure, their teams connected and their projects on track. We work alongside them as a long term partner, always ready with honest advice and quick help when it is needed. From small offices to growing companies, each client receives the same care, clear pricing and reliable support, and many of them have stayed with us for years because we treat their business like our own.</p>
  <div class="client-strip row">
    <span class="arrow" style="left:80px">&#8249;</span>
    <div class="client-name">Whitepeak</div>
    <div class="client-name">Ledgerly</div>
    <div class="client-name">Cortane</div>
    <div class="client-name">Genova</div>
    <span class="arrow" style="right:80px">&#8250;</span>
  </div>
</section>

<section class="team">
  <div class="team-intro">
    <h2>OUR TEAM</h2>
    <p>Our team brings years of hands-on experience and a friendly approach to every job.</p>
    <div class="team-arrows">
      <span><svg width="10" height="12" viewBox="0 0 10 12"><path d="M8 1L2 6l6 5" fill="none" stroke="#333" stroke-width="2"/></svg></span>
      <span><svg width="10" height="12" viewBox="0 0 10 12"><path d="M2 1l6 5-6 5" fill="none" stroke="#333" stroke-width="2"/></svg></span>
    </div>
  </div>
  <div class="team-photo" style="width:254px;background:linear-gradient(160deg,#e9ecef,#9aa3aa)" role="img" aria-label="Portrait photo of a team member in a business shirt"></div>
  <div class="team-photo" style="width:240px;background:linear-gradient(160deg,#f4f1ec,#c9c1b6)" role="img" aria-label="Portrait photo of a team member in a bright office"></div>
  <div class="team-photo" style="width:254px;background:linear-gradient(160deg,#dfe3e6,#6f7a82)" role="img" aria-label="Portrait photo of a team member in a suit"></div>
  <div class="team-photo" style="width:216px;background:linear-gradient(160deg,#e6e2dc,#a49a8e)" role="img" aria-label="Portrait photo of a smiling team member"></div>
</section>

<section class="contact">
  <h2 class="section-title">CONTACT INFO</h2>
  <p class="contact-lead">Still haven't found what you are looking for? Get in touch and our team will reply within one business day, or send us an email at <a>info@hcsgmail.com</a></p>
  <div class="contact-info">
    <div class="line"><svg width="20" height="20" viewBox="0 0 24 24"><path d="M6 2l4 4-2 3c1 3 4 6 7 7l3-2 4 4-3 4C10 21 3 14 2 5z" fill="#fff"/></svg><span class="phone">123-456-7890</span></div>
    <div class="line"><svg width="20" height="22" viewBox="0 0 20 24"><path d="M10 1a8 8 0 00-8 8c0 6 8 14 8 14s8-8 8-14a8 8 0 00-8-8z" fill="#fff"/><circle cx="10" cy="9" r="3" fill="#1b1b1b"/></svg><span>Harbourline Computing Services Group<br>14 Wharf Street, Level 3,<br>Riverside QLD 4000</span></div>
    <div class="social" aria-label="Social links"><span></span><span></span><span></span><span></span></div>
  </div>
  <form class="contact-form">
    <div class="field">Your full name</div>
    <div class="field">Your email address</div>
    <div class="field area">Message for us</div>
    <span class="btn">SEND MESSAGE</span>
  </form>
  <div class="copyright">© 2014 hcsgmail. All Rights Reserved.</div>
</section>

</body>
</html>
```